Business Card Design

Online clothing womens clothing store, I sell my clothing online and at the markets.

i would like the attached picture on the front of the card and the contact information on the back.

Industry/Entity Type

Business

Contact Information for Business Card

Marlow Thread
Karen Whitfield
(Instagram symbol) _marlow_thread_
(Facebook symbol) www.fakebookexample.com/marlowthreadau/

W : www.marlowthread.example.au
E : info@marlowthread.example.au
P : 0498716204

```html
<!DOCTYPE html>
<html lang="en">
<head>
<meta charset="utf-8">
<title>Marlow Thread – Business Card</title>
<link href="https://fonts.googleapis.com/css2?family=Open+Sans:wght@400;600;700&display=swap" rel="stylesheet">
<style>
  :root {
    --backdrop: #d9d9d9;
    --card-black: #141414;
    --band-grey: #b9b9b9;
    --band-white: #f2f2f2;
    --text-white: #ffffff;
    --photo-light: #e6ebec;
    --photo-mid: #a9b8bd;
    --photo-dark: #3c4248;
  }
  * { box-sizing: border-box; margin: 0; padding: 0; }
  html, body {
    width: 1200px; height: 900px; overflow: hidden;
    background: var(--backdrop);
    font-family: "Open Sans", Arial, sans-serif;
  }
  .sheet {
    position: relative; width: 1200px; height: 900px;
    display: flex; flex-direction: column; align-items: center; justify-content: center; gap: 50px;
  }
  .card {
    position: relative; width: 560px; height: 320px; overflow: hidden;
    box-shadow: 0 6px 18px rgba(0,0,0,0.18);
  }
  /* Front */
  .card-front__photo {
    position: absolute; inset: 0;
    background:
      radial-gradient(ellipse 45% 60% at 70% 45%, var(--photo-dark) 0%, rgba(60,66,72,0.6) 45%, rgba(169,184,189,0) 80%),
      linear-gradient(120deg, var(--photo-light) 0%, #d3dcde 45%, var(--photo-mid) 100%);
  }
  .card-front__name {
    position: absolute; left: 26px; bottom: 40px;
    color: var(--text-white); font-weight: 700; font-size: 46px; letter-spacing: 3px;
    text-transform: uppercase; line-height: 1.1;
  }
  /* Back */
  .card-back { background: var(--card-black); }
  .card-back__swoosh { position: absolute; inset: 0; }
  .card-back__holder {
    position: absolute; top: 88px; left: 0; right: 0; text-align: center;
    color: var(--text-white); font-weight: 600; font-size: 23px;
  }
  .contact-list {
    position: absolute; top: 205px; left: 0; right: 0;
    list-style: none; text-align: center; color: var(--text-white);
    font-size: 13px; line-height: 18px;
  }
  .contact-list__item { display: flex; align-items: center; justify-content: center; gap: 6px; }
  .contact-list__icon { width: 10px; height: 10px; flex: none; }
  .contact-list__mark { width: 9px; height: 9px; background: var(--text-white); flex: none; }
</style>
</head>
<body>
<main class="sheet">
  <section class="card card-front">
    <div class="card-front__photo" role="img" aria-label="Photograph of a woman's profile dissolving into dark smoke on a pale misty background"></div>
    <h1 class="card-front__name">Marlow Thread</h1>
  </section>

  <section class="card card-back">
    <svg class="card-back__swoosh" viewBox="0 0 560 320" width="560" height="320" aria-hidden="true">
      <path d="M0 20 C60 40 70 150 230 175 C360 195 470 165 560 135 L560 160 C470 195 350 215 230 200 C80 180 40 80 0 60 Z" fill="var(--band-grey)"/>
      <path d="M40 30 C120 70 120 160 240 172 C360 182 470 150 560 120 L560 132 C470 165 360 192 240 185 C110 175 100 80 40 30 Z" fill="var(--band-white)"/>
    </svg>
    <h2 class="card-back__holder">Karen Whitfield</h2>
    <ul class="contact-list">
      <li class="contact-list__item">
        <svg class="contact-list__icon" viewBox="0 0 10 10" aria-hidden="true"><path d="M1 3 Q5 0 9 3 L8 5 L6.5 4 L6.5 3 Q5 2.5 3.5 3 L3.5 4 L2 5 Z M2.5 6 H7.5 V9 H2.5 Z" fill="#fff"/></svg>
        <span>0498716204</span>
      </li>
      <li class="contact-list__item">
        <svg class="contact-list__icon" viewBox="0 0 10 10" aria-hidden="true"><rect x="0.5" y="2" width="9" height="6" fill="#fff"/><path d="M0.5 2 L5 5.5 L9.5 2" fill="none" stroke="#141414" stroke-width="0.9"/></svg>
        <span>info@marlowthread.example.au</span>
      </li>
      <li class="contact-list__item">
        <svg class="contact-list__icon" viewBox="0 0 10 10" aria-hidden="true"><path d="M4 6 L6 4 M3.5 4.5 L2 6 A1.4 1.4 0 0 0 4 8 L5.5 6.5 M6.5 5.5 L8 4 A1.4 1.4 0 0 0 6 2 L4.5 3.5" fill="none" stroke="#fff" stroke-width="1"/></svg>
        <span>www.marlowthread.example.au</span>
      </li>
      <li class="contact-list__item">
        <span class="contact-list__mark" aria-hidden="true"></span>
        <span>_marlow_thread_</span>
      </li>
      <li class="contact-list__item">
        <span class="contact-list__mark" aria-hidden="true"></span>
        <span>www.fakebookexample.com/marlowthreadau/</span>
      </li>
    </ul>
  </section>
</main>
</body>
</html>
```